Interior Design & consultancy firm requires a new business card design that is a little bit funky bu

Velbrook Design Services is a leading strategic design practice specialising in the development and implementation of strategies and design solutions for commercial workplaces across a wide variety of industries.

The company has over twenty years experience in the strategic design, development and construction of innovative and efficient workplace environments for the commercial, corporate and industrial sectors.

We believe good design and efficient workspaces can transform companies, improve people’s lives and increase productivity.

Target Market(s)

My clients are mainly Government or corporate clients wanting to create a statement with their office fitout & new furniture that reflects their corporate identity

Industry/Entity Type

Construction

Font styles to use
Sans Serif

Colors
add136

Requirements
Must have
• The business card must be easy to read, simple & highlight my name & mobile phone number
Should not have
• I do not want the card to be fussy, feature too many colours or look to busy.

```html
<!DOCTYPE html>
<html lang="en">
<head>
<meta charset="utf-8">
<title>Velbrook Design Services – Business Card</title>
<link rel="stylesheet" href="https://fonts.googleapis.com/css2?family=Open+Sans:wght@400;600;700&display=swap">
<style>
  :root {
    --stage: #e9e7e4;
    --card: #fbfbfa;
    --card-edge: #dcdad6;
    --brand-green: #2e6b38;
    --ink: #1c1c1c;
    --pattern-light: #f1f1ef;
    --pattern-dark: #dedcd8;
  }
  * { box-sizing: border-box; margin: 0; padding: 0; }
  html, body {
    width: 1200px;
    height: 800px;
    overflow: hidden;
    background: var(--stage);
    font-family: "Open Sans", Arial, sans-serif;
  }
  .canvas {
    width: 1200px;
    height: 800px;
    display: flex;
    align-items: center;
    justify-content: space-between;
    padding: 0 40px;
  }
  .card {
    width: 540px;
    height: 310px;
    background: var(--card);
    border: 1px solid var(--card-edge);
    box-shadow: 0 2px 8px rgba(0,0,0,0.12);
    position: relative;
    overflow: hidden;
  }

  /* Front side */
  .card-front {
    display: flex;
    flex-direction: column;
    align-items: center;
    justify-content: center;
    color: var(--brand-green);
    font-weight: 400;
    text-align: center;
  }
  .brand-name {
    font-size: 76px;
    line-height: 1;
    letter-spacing: 4px;
  }
  .brand-descriptor {
    font-size: 22px;
    margin-top: 10px;
    letter-spacing: 1px;
  }

  /* Back side */
  .pattern-band {
    position: absolute;
    left: 0; top: 0;
    width: 100%;
    height: 150px;
    background: linear-gradient(180deg, var(--pattern-light), var(--pattern-dark));
  }
  .back-brand {
    position: absolute;
    left: 28px;
    top: 190px;
    width: 170px;
    color: var(--brand-green);
    font-weight: 400;
    text-align: center;
  }
  .back-brand .brand-name { font-size: 34px; letter-spacing: 2px; }
  .back-brand .brand-descriptor { font-size: 10px; margin-top: 4px; letter-spacing: 0; }
  .contact {
    position: absolute;
    left: 240px;
    top: 178px;
  }
  .contact-name {
    font-size: 26px;
    font-weight: 600;
    color: var(--brand-green);
    letter-spacing: 0.5px;
  }
  .contact-role {
    font-size: 17px;
    color: var(--ink);
    margin-top: 4px;
  }
  .contact-mobile {
    font-size: 26px;
    font-weight: 700;
    color: var(--ink);
    margin-top: 6px;
  }
</style>
</head>
<body>
  <main class="canvas">
    <section class="card card-back" aria-label="Business card back">
      <div class="pattern-band" role="img" aria-label="Embossed pattern of interlocking circles on white textured card"></div>
      <div class="back-brand">
        <div class="brand-name">Velbrook</div>
        <div class="brand-descriptor">Design Services Pty Ltd</div>
      </div>
      <div class="contact">
        <p class="contact-name">Maren Ashcroft</p>
        <p class="contact-role">Director &amp; senior interior designer</p>
        <p class="contact-mobile">Mobile 0491 572 318</p>
      </div>
    </section>

    <section class="card card-front" aria-label="Business card front">
      <div class="brand-name">Velbrook</div>
      <div class="brand-descriptor">Design Services Pty Ltd</div>
    </section>
  </main>
</body>
</html>
```